Wine Label for a Sweet Wine Called "Glimmo"

We need a wine label that will be used for both a sweet red and a sweet white wine. The very important thing to remember is the target market for these wines is: young American women who love sweet wines and they also spend a lot of their money on their hair, clothes, jewelry, nails. They LOVE Glimmo (Glimmo is a word used to describe flashy accessories, jewelry, decoration.) This label needs to be eye catching, showy, fun, glittery. Please put the brand name, "Glimmo," big, and then in smaller but still readable words underneath the label or somewhere on the label: Sweet, Sophisticated, Red (or white). (An example of what I mean is attached). To differentiate between the two color wines you can suggest color changes to differentiate between the red label and the white label but the label design itself should be the same. Ultimately, the label can be the exact same label for both white and red as long as it looks good on a white wine (a greenish/yellow wine in a clear glass bottle) and a red wine (a dark color wine in a dark bottle).

I've attached an example of the text size relationship between the word Glimmo and the words to go underneath or elsewhere on the label, but you can certainly play with this-- it is just a suggestion of the text size relationship, and definitely NOT at all mandatory that you use any of these fonts.

You can pick the size of the label but try to stay within normal wine label sizes, meaning don't go bigger than approx. 3.5 inches wide and 5 inches tall.

Target Market(s)

Young American women who love sweet wines and spend a lot of money on their hair, clothes, jewelry, nails. They love Glimmo (Glimmo is a word that means flashy accessories, jewelry, decoration)

Requirements
Must have
• It needs to be flashy, glittery, fun, eye catching, memorable
Nice to have
• It shouldn't be too too ultra feminine! The target market is strong independent women and we also have men who will buy it too.

```html
<!DOCTYPE html>
<html lang="en">
<head>
<meta charset="utf-8">
<title>Glimmo Sweet Red – Label Range</title>
<link href="https://fonts.googleapis.com/css2?family=Alfa+Slab+One&family=Cinzel:wght@400;600&family=Graduate&family=Cormorant+Garamond:wght@500&display=swap" rel="stylesheet">
<style>
  :root {
    --page: #ffffff;
    --maroon: #650e18;
    --maroon-deep: #4e0a12;
    --cocoa: #3f2a28;
    --cocoa-deep: #2f1f1e;
    --navy: #1f3266;
    --navy-deep: #172750;
    --gold: #c9a55c;
    --gold-light: #e6cf93;
    --gold-soft: rgba(201, 165, 92, 0.35);
    --silver: #d9dde6;
    --silver-soft: rgba(217, 221, 230, 0.28);
  }
  * { margin: 0; padding: 0; box-sizing: border-box; }
  html, body { width: 1200px; height: 1200px; overflow: hidden; background: var(--page); }
  .range {
    width: 1200px; height: 1200px;
    display: flex; align-items: center; justify-content: center; gap: 50px;
  }
  .label {
    position: relative;
    width: 340px; height: 400px;
    overflow: hidden;
  }
  .label--ruby { background: linear-gradient(160deg, var(--maroon), var(--maroon-deep)); }
  .label--cocoa { background: linear-gradient(160deg, var(--cocoa), var(--cocoa-deep)); }
  .label--sapphire { background: linear-gradient(160deg, var(--navy), var(--navy-deep)); }

  .label__rule {
    position: absolute; inset: 12px;
    border: 1px solid var(--gold);
    opacity: 0.7;
  }
  .corner {
    position: absolute; width: 42px; height: 42px;
    background: var(--gold-soft);
  }
  .corner--tl { top: 8px; left: 8px; }
  .corner--tr { top: 8px; right: 8px; }
  .corner--bl { bottom: 8px; left: 8px; }
  .corner--br { bottom: 8px; right: 8px; }

  .emblem {
    position: absolute; left: 50%; top: 50%;
    transform: translate(-50%, -50%);
    display: flex; flex-direction: column; align-items: center; justify-content: center;
  }
  .emblem__art { position: absolute; inset: 0; }
  .emblem__frame { position: absolute; inset: 0; }

  .label--ruby .emblem { width: 270px; height: 170px; top: 52%; }
  .label--ruby .emblem__art {
    border-radius: 50%;
    background: radial-gradient(ellipse at center, rgba(201,165,92,0.18), rgba(201,165,92,0.05) 70%, transparent 72%);
  }
  .label--cocoa .emblem { width: 260px; height: 250px; top: 50%; }
  .label--cocoa .emblem__art {
    background: radial-gradient(ellipse at center, rgba(201,165,92,0.16), rgba(201,165,92,0.04) 65%, transparent 70%);
  }
  .label--sapphire .emblem { width: 316px; height: 260px; top: 48%; }
  .label--sapphire .emblem__art {
    background: radial-gradient(ellipse at center, transparent 35%, var(--silver-soft) 60%, transparent 75%);
  }

  .brand {
    position: relative;
    font-family: "Alfa Slab One", serif;
    color: var(--gold-light);
    letter-spacing: 2px;
    line-height: 1;
  }
  .label--ruby .brand { font-size: 48px; }
  .label--cocoa .brand { font-size: 44px; }
  .label--sapphire .brand {
    font-family: "Graduate", serif;
    color: var(--silver);
    font-size: 46px;
    letter-spacing: 3px;
  }

  .varietal-tag {
    position: relative;
    font-family: "Cinzel", serif;
    font-weight: 600;
    color: var(--gold);
    font-size: 11px;
    letter-spacing: 3px;
    margin-bottom: 8px;
  }
  .varietal-plaque {
    position: relative;
    margin-top: 8px;
    padding: 3px 16px;
    background: var(--gold);
    color: var(--cocoa-deep);
    font-family: "Alfa Slab One", serif;
    font-size: 17px;
    letter-spacing: 3px;
  }
  .brand-rule {
    position: relative;
    width: 150px; height: 1px; margin-top: 10px;
    background: var(--gold);
  }
  .label--sapphire .brand-rule { width: 190px; background: var(--silver); margin-top: 6px; }

  .tagline {
    position: absolute; left: 0; right: 0;
    text-align: center;
    font-family: "Cinzel", serif;
    font-size: 10px;
    letter-spacing: 1.5px;
    color: var(--gold);
  }
  .label--ruby .tagline, .label--cocoa .tagline { bottom: 40px; }
  .tagline--inline {
    position: relative;
    margin-top: 6px;
    font-family: "Cormorant Garamond", serif;
    font-weight: 500;
    font-size: 12px;
    letter-spacing: 1px;
    color: var(--silver);
  }
</style>
</head>
<body>
<main class="range">

  <section class="label label--ruby">
    <div class="label__rule"></div>
    <div class="corner corner--tl" role="img" aria-label="gold corner flourish"></div>
    <div class="corner corner--tr" role="img" aria-label="gold corner flourish"></div>
    <div class="corner corner--bl" role="img" aria-label="gold corner flourish"></div>
    <div class="corner corner--br" role="img" aria-label="gold corner flourish"></div>
    <div class="emblem">
      <div class="emblem__art" role="img" aria-label="gold filigree cartouche"></div>
      <svg class="emblem__frame" viewBox="0 0 270 170" aria-hidden="true">
        <ellipse cx="135" cy="85" rx="128" ry="78" fill="none" stroke="#c9a55c" stroke-width="1.5"/>
        <ellipse cx="135" cy="85" rx="120" ry="71" fill="none" stroke="#c9a55c" stroke-width="0.6"/>
      </svg>
      <span class="varietal-tag">RED</span>
      <span class="brand">GLIMMO</span>
      <span class="brand-rule"></span>
    </div>
    <p class="tagline">SWEET | SOPHISTICATED</p>
  </section>

  <section class="label label--cocoa">
    <div class="label__rule"></div>
    <div class="corner corner--tl" role="img" aria-label="gold corner flourish"></div>
    <div class="corner corner--tr" role="img" aria-label="gold corner flourish"></div>
    <div class="corner corner--bl" role="img" aria-label="gold corner flourish"></div>
    <div class="corner corner--br" role="img" aria-label="gold corner flourish"></div>
    <div class="emblem">
      <div class="emblem__art" role="img" aria-label="gold art deco ornament"></div>
      <svg class="emblem__frame" viewBox="0 0 260 250" aria-hidden="true">
        <path d="M130 6 L210 40 L210 90 L254 125 L210 160 L210 210 L130 244 L50 210 L50 160 L6 125 L50 90 L50 40 Z" fill="none" stroke="#c9a55c" stroke-width="1.5"/>
        <path d="M130 16 L200 46 L200 95 L240 125 L200 155 L200 204 L130 234 L60 204 L60 155 L20 125 L60 95 L60 46 Z" fill="none" stroke="#c9a55c" stroke-width="0.6"/>
      </svg>
      <span class="brand">GLIMMO</span>
      <span class="varietal-plaque">RED</span>
    </div>
    <p class="tagline">SWEET | SOPHISTICATED</p>
  </section>

  <section class="label label--sapphire">
    <div class="emblem">
      <div class="emblem__art" role="img" aria-label="silver baroque scroll frame"></div>
      <span class="brand">GLIMMO</span>
      <span class="brand-rule"></span>
      <span class="tagline tagline--inline">Sweet | Sophisticated | Red</span>
    </div>
  </section>

</main>
</body>
</html>
```